Business card design needed

I need a business card design for a dog walking, dog minding and dog training business. Please refer to my website for the basic company colours and fonts I'm after. Planning on a double sided card, so all information doesn't need to be on the 'front' side.
Cheers

Industry/Entity Type

Dog Training

Contact Information for Business Card

Bramble Paws - gathering hounds
Rua 0498376214
bramblepaws.com.au
-walking
-holiday stays
-onsite care
-training and behavioural consultations

```html
<!DOCTYPE html>
<html lang="en">
<head>
<meta charset="utf-8">
<title>Bramble Paws – Business Card</title>
<link rel="stylesheet" href="https://fonts.googleapis.com/css2?family=Questrial&family=Poiret+One&display=swap">
<style>
  :root {
    --orange: #f15a24;
    --cream: #f0ece6;
    --white: #ffffff;
    --ink: #1e1e1e;
    --service: #f8d3c2;
    --photo-light: #e2c9a3;
    --photo-dark: #b99466;
  }
  * { margin: 0; padding: 0; box-sizing: border-box; }
  html, body {
    width: 1200px; height: 900px; overflow: hidden;
    background: var(--white);
    font-family: "Questrial", "Century Gothic", sans-serif;
  }
  .canvas { position: relative; width: 1200px; height: 900px; }
  .card {
    position: absolute; left: 285px; width: 660px; height: 411px; overflow: hidden;
  }
  /* Front */
  .card--front { top: 39px; background: var(--cream); }
  .card__curves { position: absolute; inset: 0; }
  .puppy-photo {
    position: absolute; left: 280px; top: 130px; width: 105px; height: 148px;
    border-radius: 48px 48px 30px 30px;
    background: radial-gradient(ellipse at 50% 40%, var(--photo-light), var(--photo-dark) 85%, var(--cream) 100%);
    opacity: .9;
  }
  .tagline {
    position: absolute; left: 0; width: 660px; top: 280px;
    text-align: center; font-size: 15px; color: var(--ink); letter-spacing: .2px;
  }
  .front-brand {
    position: absolute; right: 10px; top: 349px; text-align: right; color: var(--white);
    white-space: nowrap;
  }
  .front-brand__name { font-size: 24px; letter-spacing: .5px; line-height: 1; text-transform: uppercase; }
  .front-brand__url { font-size: 16px; margin-top: 8px; letter-spacing: .3px; }
  /* Back */
  .card--back { top: 476px; background: var(--orange); color: var(--white); }
  .back-brand {
    position: absolute; left: 0; width: 660px; top: 53px; text-align: center;
    font-size: 62px; line-height: 62px; letter-spacing: 2px; text-transform: uppercase;
    white-space: nowrap;
  }
  .divider {
    position: absolute; left: 327px; top: 159px; width: 1px; height: 142px; background: var(--white);
  }
  .contact {
    position: absolute; left: 95px; top: 206px; white-space: nowrap;
    font-family: "Poiret One", "Questrial", sans-serif; font-size: 26px; font-weight: 400;
  }
  .contact__name { color: var(--white); margin-right: 14px; }
  .contact__phone { color: var(--ink); }
  .services {
    position: absolute; left: 399px; top: 166px; list-style: none; white-space: nowrap;
    font-family: "Poiret One", "Questrial", sans-serif; font-size: 15px; line-height: 17.6px;
    color: var(--service); letter-spacing: .6px;
  }
  .credentials {
    position: absolute; left: 28px; top: 364px; font-size: 13px; line-height: 16px; color: var(--white);
    white-space: nowrap;
  }
</style>
</head>
<body>
<div class="canvas">
  <section class="card card--front">
    <svg class="card__curves" viewBox="0 0 660 411" width="660" height="411" aria-hidden="true">
      <path d="M0 0 H145 Q45 45 0 133 Z" fill="var(--orange)"/>
      <path d="M352 411 Q560 335 660 243 V411 Z" fill="var(--orange)"/>
    </svg>
    <div class="puppy-photo" role="img" aria-label="Photo of a golden puppy sitting and looking up"></div>
    <p class="tagline">gathering hounds.</p>
    <div class="front-brand">
      <div class="front-brand__name">Bramble Paws</div>
      <div class="front-brand__url">bramblepaws.com.au</div>
    </div>
  </section>

  <section class="card card--back">
    <div class="back-brand">Bramble Paws</div>
    <div class="divider"></div>
    <p class="contact"><span class="contact__name">Rua</span><span class="contact__phone">0498376214</span></p>
    <ul class="services">
      <li>Group dog walk</li>
      <li>Group dog walk casual</li>
      <li>Solo dog walk</li>
      <li>Solo dog walk casual</li>
      <li>On site, in home care</li>
      <li>Hound holiday stay</li>
    </ul>
    <p class="credentials">*Bramble Paws is run by a qualified dog behaviourist and trainer who is also an accredited pet first aider.<br>We hold pet care specific public liability insurance and carry a current police check.</p>
  </section>
</div>
</body>
</html>
```